Design a modern, classy & professional business card for an online real estate agency, specializing in medium-luxury properties in Thailand and later in Singapore and UK.

Possible design ideas so far: (not essential)

- curved corner(s) to the card, white on front & turquoise on back or visa versa.

- front of card - clear and simple, company name in metallic grey/monochrome, logo graphic & company name on front in spot UV or embossed/debossed effect.

- back of card - large, close-cropped, 'ghost' patterns of the C-shaped curves of logo, or company name repeated on back of card in spot UV.

Target Market(s)

- young to middle-aged professionals mainly (but ideally should design should suit all)

- UK, US,EU,AUS & ASIAN mainly (but ideally should design should suit all countries)

Industry/Entity Type

Real Estate

Requirements
Must have
• THEME:
- Luxurious & Modern
- Clean & striking
- Unique & creative

INFO:
- Logo & company name on front
- Contact details on back:

Tobias Hennlund
Managing Director

www.velmontestates.asia
www.velmontestates.co.uk

Tel: 083-274-6159
email: tobias@velmontestates.asia

(contact details can be displayed in any order as suites design.)

Nice to have
• - curved corner(s) to the card, white on front & turquoise on back or visa versa.

Should not have
• - No generic images of properties, palm trees/coconut trees etc.

- No other other bold colors, except for main turquoise, grey, metallic white & black theme.

- No obvious business card templates

```html
<!DOCTYPE html>
<html lang="en">
<head>
<meta charset="utf-8">
<title>Velmont Estates – Business Card</title>
<link href="https://fonts.googleapis.com/css2?family=Cormorant+Garamond:wght@500&family=Russo+One&family=Comfortaa:wght@500&display=swap" rel="stylesheet">
<style>
  :root{
    --stage:#2b2b2d;
    --card-white:#ffffff;
    --card-white-shade:#e4e4e6;
    --turquoise:#5fc3c2;
    --turquoise-deep:#4fb3b2;
    --turquoise-light:#7fd3d1;
    --grey:#7a7a7c;
    --grey-dark:#555557;
    --silver-hi:#ffffff;
    --silver-lo:#8d9596;
    --contact:#ffffff;
  }
  *{margin:0;padding:0;box-sizing:border-box}
  html,body{width:1200px;height:900px;overflow:hidden}
  body{background:var(--stage);position:relative;font-family:"Comfortaa",sans-serif}

  .card{position:absolute;border-radius:34px;box-shadow:0 18px 40px rgba(0,0,0,.45)}

  /* front */
  .card--front{
    left:70px;top:60px;width:640px;height:366px;
    background:linear-gradient(160deg,var(--card-white) 45%,var(--card-white-shade));
  }
  .front__person{position:absolute;right:46px;top:38px;text-align:right;color:var(--turquoise-deep);font-family:"Russo One",sans-serif;text-transform:uppercase}
  .front__name{font-size:19px;letter-spacing:.5px}
  .front__role{font-size:10px;letter-spacing:.6px;margin-top:3px}
  .brand{position:absolute;left:70px;top:150px;display:flex;align-items:center;gap:26px}
  .brand__square{width:130px;height:130px;background:var(--turquoise)}
  .brand__name{font-family:"Cormorant Garamond",serif;font-weight:500;font-size:60px;color:var(--grey);letter-spacing:1px;line-height:1}

  /* back */
  .card--back{
    left:470px;top:420px;width:670px;height:400px;
    background:linear-gradient(150deg,var(--turquoise-light),var(--turquoise) 45%,var(--turquoise-deep));
  }
  .back__person{position:absolute;left:56px;top:118px;text-align:right;width:260px;font-family:"Russo One",sans-serif;text-transform:uppercase}
  .back__name{
    font-size:24px;letter-spacing:1px;
    background:linear-gradient(180deg,var(--silver-hi) 20%,var(--silver-lo) 80%);
    -webkit-background-clip:text;background-clip:text;color:transparent;
    filter:drop-shadow(1px 2px 1px rgba(0,0,0,.35));
  }
  .back__role{font-size:11px;color:var(--grey-dark);letter-spacing:.6px;margin-top:4px}
  .back__divider{position:absolute;left:332px;top:132px;width:3px;height:118px;background:linear-gradient(180deg,var(--silver-hi),var(--grey-dark))}
  .contact{position:absolute;left:350px;top:150px;list-style:none;color:var(--contact);font-size:14px;line-height:22px;text-shadow:1px 1px 1px rgba(0,0,0,.3)}
  .contact li{display:flex;align-items:center;gap:8px}
  .contact svg{width:11px;height:11px;flex:none}
</style>
</head>
<body>

<section class="card card--front">
  <div class="front__person">
    <p class="front__name">Tobias Hennlund</p>
    <p class="front__role">Managing Director</p>
  </div>
  <div class="brand">
    <span class="brand__square"></span>
    <span class="brand__name">Velmont Estates</span>
  </div>
</section>

<section class="card card--back">
  <div class="back__person">
    <p class="back__name">Tobias Hennlund</p>
    <p class="back__role">Managing Director</p>
  </div>
  <span class="back__divider"></span>
  <ul class="contact">
    <li><svg viewBox="0 0 12 12"><circle cx="6" cy="6" r="5" fill="none" stroke="#fff" stroke-width="1.4"/><path d="M1 6h10M6 1c2.5 3 2.5 7 0 10M6 1c-2.5 3-2.5 7 0 10" fill="none" stroke="#fff" stroke-width="1"/></svg>www.velmontestates.asia</li>
    <li><svg viewBox="0 0 12 12"><circle cx="6" cy="6" r="5" fill="none" stroke="#fff" stroke-width="1.4"/><path d="M1 6h10M6 1c2.5 3 2.5 7 0 10M6 1c-2.5 3-2.5 7 0 10" fill="none" stroke="#fff" stroke-width="1"/></svg>www.velmontestates.co.uk</li>
    <li><svg viewBox="0 0 12 12"><path d="M2 1h3l1 3-2 1c1 2 2 3 3 3l1-2 3 1v3c-6 0-10-4-9-9z" fill="#fff"/></svg>Tel: 083-274-6159</li>
    <li><svg viewBox="0 0 12 12"><rect x="1" y="2.5" width="10" height="7" fill="none" stroke="#fff" stroke-width="1.2"/><path d="M1 2.5l5 4 5-4" fill="none" stroke="#fff" stroke-width="1.2"/></svg>email: tobias@velmontestates.asia</li>
  </ul>
</section>

</body>
</html>
```